Chimney Service company needs new business card design

We need a updated business card with our new logo added. We provide a full range of chimney services throughout Vermont and New Hampshire. The business card will be one sided and color. Attached is our current business card another document showing all the information we would like on the card.
We dont like a lot of flashy colors.... here is a link to our website to get an idea of our branding www.flueguardianvt.example

Target Market(s)

homeowners

Industry/Entity Type

Business

Contact Information for Business Card

See attached sheet for content.

Font styles to use
Serif
Sans Serif

Requirements
Must have
• all information provided on separate sheet
Should not have
• Additional information that may clogg up design

```html
<!DOCTYPE html>
<html lang="en">
<head>
<meta charset="utf-8">
<title>Flue Guardian – Business Card</title>
<link rel="stylesheet" href="https://fonts.googleapis.com/css2?family=Cinzel:wght@500&family=Open+Sans:wght@400;600&family=Archivo:wght@800&display=swap">
<style>
  :root {
    --backdrop: #c2c2c2;
    --card-dark: #2f2f2f;
    --card-light: #f2f2f2;
    --ink: #2b2b2b;
    --ink-soft: #3a3a3a;
    --brand-red: #8c0b0b;
    --accent-red: #b5171b;
    --white: #ffffff;
  }
  * { box-sizing: border-box; margin: 0; padding: 0; }
  html, body { width: 1200px; height: 576px; overflow: hidden; }
  body {
    background: var(--backdrop);
    position: relative;
    font-family: "Open Sans", Arial, sans-serif;
  }
  .card {
    position: absolute;
    top: 138px;
    width: 484px;
    height: 292px;
    border-radius: 14px;
    overflow: hidden;
  }
  /* Front */
  .card--front { left: 82px; background: var(--card-dark); }
  .front-lockup {
    position: absolute;
    left: 0; right: 0; top: 78px;
    display: flex; flex-direction: column; align-items: center; gap: 22px;
  }
  .brand-square {
    width: 104px; height: 104px;
    border: 10px solid var(--white);
  }
  .brand-name {
    font-family: "Cinzel", Georgia, serif;
    font-weight: 500;
    font-size: 24px;
    letter-spacing: 1px;
    white-space: nowrap;
  }
  .card--front .brand-name { color: var(--white); }

  /* Back */
  .card--back { left: 602px; background: var(--card-light); }
  .back-lockup {
    position: absolute;
    left: 19px; width: 220px; top: 62px;
    display: flex; flex-direction: column; align-items: center; gap: 20px;
  }
  .back-lockup .brand-square { border-color: var(--ink); width: 114px; height: 114px; }
  .card--back .brand-name { color: var(--ink); font-size: 23px; }

  .services {
    position: absolute; left: 266px; top: 28px;
    list-style: none;
    font-size: 12.5px; color: var(--ink-soft);
    line-height: 16.6px;
  }
  .services li { display: flex; align-items: center; gap: 7px; }
  .services li::before {
    content: ""; width: 6px; height: 6px; border-radius: 50%;
    background: var(--accent-red); flex: none;
  }
  .region {
    position: absolute; left: 264px; top: 124px;
    font-family: "Archivo", Arial, sans-serif; font-weight: 800;
    font-size: 17.5px; line-height: 21px; color: var(--ink-soft);
    white-space: nowrap;
  }
  .since {
    position: absolute; left: 264px; top: 166px; width: 162px;
    display: flex; align-items: center; gap: 6px;
    font-size: 9.5px; color: var(--ink-soft);
  }
  .since::before, .since::after {
    content: ""; flex: 1; height: 1.5px; background: var(--brand-red);
  }
  .contacts {
    position: absolute; left: 266px; top: 188px;
    list-style: none; font-size: 12.5px; color: var(--ink-soft);
    line-height: 19.2px;
  }
  .contacts li { display: flex; align-items: center; gap: 11px; }
  .contacts svg { width: 11px; height: 11px; fill: var(--brand-red); flex: none; }
  .contacts .web-domain { color: var(--brand-red); }
  .trust-band {
    position: absolute; left: 0; right: 0; bottom: 0; height: 23px;
    background: var(--brand-red); color: var(--white);
    display: flex; align-items: center; justify-content: center; gap: 14px;
    font-size: 11.5px;
  }
</style>
</head>
<body>
  <section class="card card--front" aria-label="Card front">
    <div class="front-lockup">
      <div class="brand-square"></div>
      <div class="brand-name">FLUE GUARDIAN</div>
    </div>
  </section>

  <section class="card card--back" aria-label="Card back">
    <div class="back-lockup">
      <div class="brand-square"></div>
      <div class="brand-name">FLUE GUARDIAN</div>
    </div>

    <ul class="services">
      <li>Full Masonry Services</li>
      <li>Historic chimney restoration</li>
      <li>Stainless steel liners</li>
      <li>New Chimney installations</li>
      <li>Fully Certified Chimney sweeps</li>
    </ul>

    <div class="region">SERVING VALLEY AND<br>NORTH COUNTY</div>
    <div class="since">SINCE 1994</div>

    <ul class="contacts">
      <li>
        <svg viewBox="0 0 12 12" aria-hidden="true"><path d="M1 4c0-1.5 2-3 5-3s5 1.5 5 3v1H8.5V4h-5v1H1zM3 6h6l1.5 5h-9z"/></svg>
        555-010-0147
      </li>
      <li>
        <svg viewBox="0 0 12 12" aria-hidden="true"><path d="M0 2h12v1L6 7 0 3zM0 4.2l6 4 6-4V10H0z"/></svg>
        info@flueguardian.example
      </li>
      <li>
        <svg viewBox="0 0 12 12" aria-hidden="true"><circle cx="6" cy="6" r="5.2" fill="none" stroke="#8c0b0b" stroke-width="1.2"/><path d="M0.8 6h10.4M6 0.8v10.4" stroke="#8c0b0b" stroke-width="1"/><ellipse cx="6" cy="6" rx="2.3" ry="5.2" fill="none" stroke="#8c0b0b" stroke-width="1"/></svg>
        <span>www.<span class="web-domain">flueguardianvt</span>.example</span>
      </li>
    </ul>

    <div class="trust-band">
      <span>Fully Insured – Free Estimates</span>
      <span>|</span>
      <span>Family Owned &amp; Operated</span>
    </div>
  </section>
</body>
</html>
```